Copperleaf Roofing Business Card

This is my current business card. But I’d like to make some changes. Somewhere on the card I’d like to list some of the services we offer. Maybe on the back? But I’d still like to keep the red. White and black modern look.

-residential & commercial roofing
-Roof Repairs & Maintenance
-Storm Damage & Insurance Claims specialist
-Christmas Lights and permanent Christmas lights
Fencing. Windows. Gutters. Siding. Sheetrock, painting.

```html
<!DOCTYPE html>
<html lang="en">
<head>
<meta charset="utf-8">
<title>Copperleaf Roofing Co. – Business Card</title>
<link href="https://fonts.googleapis.com/css2?family=Audiowide&family=Montserrat:wght@400;500&display=swap" rel="stylesheet">
<style>
  :root {
    --red: #e31e24;
    --red-dark: #6b0d0f;
    --black: #111111;
    --white: #ffffff;
    --ink: #1a1a1a;
    --page: #d4d5d7;
  }
  * { box-sizing: border-box; margin: 0; padding: 0; }
  html, body { width: 900px; height: 1200px; overflow: hidden; }
  body {
    background: var(--page);
    font-family: "Montserrat", sans-serif;
    color: var(--ink);
    position: relative;
  }
  .card {
    position: absolute;
    left: 120px;
    width: 660px;
    height: 380px;
    border-radius: 14px;
    overflow: hidden;
  }
  /* ---------- front ---------- */
  .card-front { top: 200px; }
  .tartan-field {
    position: absolute; inset: 0;
    background:
      linear-gradient(180deg, transparent 0 40%, rgba(0,0,0,.55) 40% 64%, transparent 64%),
      linear-gradient(180deg, var(--red-dark) 0%, var(--red) 35%, var(--red-dark) 100%);
  }
  .front-mark {
    position: absolute;
    left: 255px; top: 75px;
    width: 150px; height: 150px;
    border: 4px solid var(--white);
    border-radius: 50%;
  }
  .front-name {
    position: absolute;
    left: 0; right: 0; top: 228px;
    text-align: center;
    font-family: "Audiowide", sans-serif;
    color: var(--white);
    line-height: 1.05;
  }
  .front-name .line-1 { display: block; font-size: 38px; letter-spacing: 1px; }
  .front-name .line-2 { display: block; font-size: 27px; letter-spacing: 1px; }

  /* ---------- back ---------- */
  .card-back { top: 620px; background: var(--white); }
  .back-mark {
    position: absolute;
    left: 467px; top: 29px;
    width: 112px; height: 112px;
    border-radius: 50%;
    background: var(--red);
  }
  .back-name {
    position: absolute;
    right: 22px; top: 150px;
    text-align: center;
    font-family: "Audiowide", sans-serif;
    color: var(--red);
    line-height: 1.1;
  }
  .back-name .line-1 { display: block; font-size: 26px; letter-spacing: .5px; }
  .back-name .line-2 { display: block; font-size: 19px; letter-spacing: .5px; }

  .person {
    position: absolute; left: 28px; top: 172px;
  }
  .person-name {
    font-family: "Audiowide", sans-serif;
    font-size: 22px;
    letter-spacing: .5px;
    color: var(--black);
  }
  .person-name .surname { color: var(--red); }
  .person-role { font-size: 13px; margin-top: 2px; }

  .rule {
    position: absolute; left: 26px; top: 226px;
    width: 610px; height: 1px; background: var(--red);
  }

  .services {
    position: absolute; right: 22px; top: 240px;
    list-style: none;
    text-align: right;
    font-size: 14.5px;
    line-height: 17px;
  }
  .services li {
    position: relative;
    padding-right: 12px;
    margin-bottom: 6px;
  }
  .services li::after {
    content: "";
    position: absolute; right: 0; top: 50%;
    width: 5px; height: 5px; margin-top: -2px;
    border-radius: 50%; background: var(--red);
  }

  .contacts {
    position: absolute; left: 30px; top: 290px;
    list-style: none;
    font-size: 14.5px;
  }
  .contacts li {
    display: flex; align-items: center; gap: 8px;
    height: 24px;
  }
  .contacts svg { width: 14px; height: 14px; fill: var(--red); flex: none; }

  .base-band {
    position: absolute; left: 0; bottom: 0;
    width: 660px; height: 18px;
  }
</style>
</head>
<body>

<section class="card card-front" aria-label="Card front">
  <div class="tartan-field" role="img" aria-label="Red, black and white tartan plaid pattern"></div>
  <div class="front-mark"></div>
  <h1 class="front-name">
    <span class="line-1">COPPERLEAF</span>
    <span class="line-2">ROOFING CO.</span>
  </h1>
</section>

<section class="card card-back" aria-label="Card back">
  <div class="back-mark"></div>
  <h2 class="back-name">
    <span class="line-1">COPPERLEAF</span>
    <span class="line-2">ROOFING CO.</span>
  </h2>

  <div class="person">
    <p class="person-name">DEAN <span class="surname">MARLOW</span></p>
    <p class="person-role">Owner</p>
  </div>

  <div class="rule"></div>

  <ul class="services">
    <li>residential &amp; commercial roofing</li>
    <li>Roof Repairs &amp; Maintenance</li>
    <li>Storm Damage &amp;<br>Insurance Claims specialist</li>
    <li>Fencing. Windows. Gutters.<br>Siding. Sheetrock, painting</li>
  </ul>

  <ul class="contacts">
    <li>
      <svg viewBox="0 0 24 24" aria-hidden="true"><path d="M6.6 10.8a15.1 15.1 0 0 0 6.6 6.6l2.2-2.2c.3-.3.7-.4 1-.2 1.1.4 2.3.6 3.6.6.6 0 1 .4 1 1V20c0 .6-.4 1-1 1A17 17 0 0 1 3 4c0-.6.4-1 1-1h3.5c.6 0 1 .4 1 1 0 1.3.2 2.5.6 3.6.1.3 0 .7-.2 1z"/></svg>
      <span>682-555-0148</span>
    </li>
    <li>
      <svg viewBox="0 0 24 24" aria-hidden="true"><path d="M2 5h20v14H2z" fill="none"/><path d="M2 6.5 12 13l10-6.5V19H2z"/><path d="M2 5h20l-10 6.5z"/></svg>
      <span>dean@copperleafroofing.com</span>
    </li>
    <li>
      <svg viewBox="0 0 24 24" aria-hidden="true"><circle cx="12" cy="12" r="10"/><path d="M2 12h20M12 2c3 3 3 17 0 20M12 2c-3 3-3 17 0 20" stroke="#fff" stroke-width="1.5" fill="none"/></svg>
      <span>www.copperleafroofing.com</span>
    </li>
  </ul>

  <svg class="base-band" viewBox="0 0 660 18" preserveAspectRatio="none" aria-hidden="true">
    <polygon points="0,2 342,2 326,18 0,18" fill="#111111"/>
    <polygon points="350,2 660,2 660,18 334,18" fill="#e31e24"/>
  </svg>
</section>

</body>
</html>
```